Vernac Law Business cards and stationary design project

We are looking for a stationary design for business cards (double sided), 8x10, 5x7, and legal and standard envelopes.

We would like the design to match the logo that we have already.
Color palate preferred is Teal, White, grey and any others that will look good for a professional law firm.

We would like this statement: "RELATIONSHIPS. RESPECT. RESULT" to be on the back of the business cards and maybe on the stationary if it looks good.

Please see link to website for more information: www.vernac-law.example

Target Market(s)

Potential clients that need Attorney services.

Industry/Entity Type

Law Firm

Contact Information for Business Card

We would like the front and back to be two different colors. Current business cards are teal front, grey back and are a vertical design. We are open to options with colors.

Font styles to use
Serif

Colors
33a6d7
33b8a4
b9b9b9
5c5c5c

Requirements
Must have
• Logo supplied needs to go on the card and stationary.
• Match website color palate, www.vernac-law.example
• Be professional and not too wordy.
• Criminal Law, Civil Litigation, Personal Injury, Restraining Orders need to be on the card.
Nice to have
• RELATIONSHIPS. RESPECT. RESULTS. on the back of the card.
Should not have
• Not be too busy/wordy or too flashy.

```html
<!DOCTYPE html>
<html lang="en">
<head>
<meta charset="utf-8">
<title>Vernac Law — Business Card</title>
<link href="https://fonts.googleapis.com/css2?family=Playfair+Display+SC&family=Source+Sans+3:wght@400;600&display=swap" rel="stylesheet">
<style>
  :root {
    --teal: #0e8597;
    --white: #ffffff;
    --ink: #1c1c1c;
    --backdrop: #1b1b1b;
  }
  * { margin: 0; padding: 0; box-sizing: border-box; }
  html, body { width: 1200px; height: 900px; overflow: hidden; }
  body {
    background: var(--backdrop);
    font-family: "Source Sans 3", "Helvetica Neue", Arial, sans-serif;
    position: relative;
  }
  .card {
    position: absolute;
    top: 170px;
    width: 347px;
    height: 561px;
  }
  .card--front { left: 259px; background: var(--white); color: var(--ink); }
  .card--back { left: 631px; background: var(--teal); color: var(--white); }

  .tab {
    position: absolute;
    left: 102px;
    width: 143px;
    height: 29px;
    background: var(--teal);
  }
  .tab--top { top: 0; }
  .tab--bottom { bottom: 0; }

  .firm-name {
    position: absolute;
    left: 0; right: 0;
    text-align: center;
    font-family: "Playfair Display SC", Georgia, serif;
    font-weight: 400;
    letter-spacing: 1px;
  }
  .card--front .firm-name { top: 140px; font-size: 34px; color: var(--teal); }
  .card--back .firm-name { top: 402px; font-size: 42px; color: var(--white); }

  .block {
    position: absolute;
    left: 0; right: 0;
    text-align: center;
  }
  .person { top: 218px; }
  .person__name { font-size: 21px; font-weight: 600; color: var(--teal); line-height: 26px; }
  .person__title { font-size: 15px; line-height: 19px; }

  .contact { top: 295px; font-size: 15px; line-height: 23px; }
  .contact__row { display: flex; justify-content: center; align-items: center; gap: 3px; }
  .contact__row svg { width: 11px; height: 11px; fill: var(--teal); }

  .address { top: 406px; font-size: 15px; line-height: 17px; }

  .practice { top: 458px; font-size: 15px; line-height: 20px; font-weight: 600; color: var(--teal); }

  .tagline {
    position: absolute;
    left: 0; right: 0;
    top: 510px;
    text-align: center;
    font-size: 17px;
    font-weight: 600;
    letter-spacing: 0.2px;
  }
</style>
</head>
<body>
  <section class="card card--front" aria-label="Business card front">
    <div class="tab tab--top"></div>
    <div class="firm-name">Vernac Law</div>

    <div class="block person">
      <div class="person__name">Daniel Marlow</div>
      <div class="person__title">Managing Director</div>
    </div>

    <div class="block contact">
      <div class="contact__row">
        <svg viewBox="0 0 12 12" aria-hidden="true"><path d="M2.5 1 L4.5 1 L5 3.5 L3.8 4.4 Q4.9 6.9 7.6 8.2 L8.5 7 L11 7.5 L11 9.5 Q10.5 11 9 11 Q1 10 1 2.5 Q1 1 2.5 1 Z"/></svg>
        <span>(055)-318-2046</span>
      </div>
      <div class="contact__row">
        <svg viewBox="0 0 12 12" aria-hidden="true"><path d="M3 1 H8 L9 2 V4 H3 Z M1 4.5 H11 V11 H1 Z M3 6 V7 H5 V6 Z M6 6 V7 H8 V6 Z M3 8 V9 H5 V8 Z M6 8 V9 H8 V8 Z"/></svg>
        <span>555-274-9031</span>
      </div>
      <div class="contact__row">
        <svg viewBox="0 0 12 12" aria-hidden="true"><path d="M1 2.5 H11 V3.2 L6 6.5 L1 3.2 Z M1 4.4 L6 7.7 L11 4.4 V10 H1 Z"/></svg>
        <span>info@vernac-law.example</span>
      </div>
      <div class="contact__row">
        <svg viewBox="0 0 12 12" aria-hidden="true"><circle cx="6" cy="6" r="5"/></svg>
        <span>www.vernac-law.example</span>
      </div>
    </div>

    <div class="block address">
      <div>480, Harbor Lane Suite 2</div>
      <div>Westbrook, 90417</div>
    </div>

    <div class="block practice">
      <div>Practice areas, Criminal Law,</div>
      <div>Civil Litigation/Personal Injury</div>
      <div>Restraining Orders</div>
    </div>

    <div class="tab tab--bottom"></div>
  </section>

  <section class="card card--back" aria-label="Business card back">
    <div class="firm-name">Vernac Law</div>
    <div class="tagline">RELATIONSHIPS. RESPECT. RESULT</div>
  </section>
</body>
</html>
```